Business card for my new company (Accounting firm)

I need a business card for my new business Brightwell Advisory and Ledger SA. Our services are accounting, tax, audit and financial management. Our customers are small companies, start-ups and new companies. The final design has to show financial security, trust and growth. Please find our logo attached to the business card. Text for the business card: Brightwell Advisory and Ledger SA Tomas Varenholt Director and Founder Certified Accountant Tel. 022 418 57 34 tv@clairevalconseil.ch www.clairevalconseil.ch Rue des Vergières 27 1201 Geneva
Target Market(s)
Our customers are small companies, start-ups and new companies.
Industry/Entity Type
Finance And Accounting
Contact Information for Business Card
Claireval Conseil et Comptes SA
Tomas Varenholt
Directeur et Fondateur
Expert-comptable diplômé
Tél. 022 418 57 34
tv@clairevalconseil.ch
www.clairevalconseil.ch
Rue des Vergières 27
1201 Genève

```html
<!DOCTYPE html>
<html lang="fr">
<head>
<meta charset="utf-8">
<title>Brightwell Advisory and Ledger SA – Carte de visite</title>
<link rel="stylesheet" href="https://fonts.googleapis.com/css2?family=Montserrat:wght@400;500;600;700&display=swap">
<style>
  :root {
    --backdrop: #2b2b2d;
    --brand-blue: #2aa8df;
    --brand-blue-deep: #1f8fc6;
    --brand-navy: #1d5f93;
    --ink: #2a2a2a;
    --ink-soft: #444;
    --paper: #ffffff;
    --paper-shade: #e9e9ea;
    --rule: #2b2b2b;
  }
  * { box-sizing: border-box; margin: 0; padding: 0; }
  html, body {
    width: 1200px; height: 997px; overflow: hidden;
    background: var(--backdrop);
    font-family: "Montserrat", Arial, sans-serif;
  }
  .sheet {
    position: relative; width: 1200px; height: 997px;
    display: flex; flex-direction: column; align-items: center; justify-content: center; gap: 44px;
  }
  .card {
    position: relative; width: 760px; height: 434px;
    border-radius: 30px; overflow: hidden;
  }

  /* Back of card */
  .card--back {
    background: linear-gradient(160deg, #35b6ea 0%, var(--brand-blue) 55%, var(--brand-blue-deep) 100%);
    color: var(--paper);
    display: flex; flex-direction: column; align-items: center; justify-content: center;
    text-align: center;
  }
  .card--back .wordmark { color: var(--paper); margin-bottom: 46px; }
  .services-title {
    font-size: 17px; font-weight: 700; letter-spacing: 0.5px;
    text-decoration: underline; text-underline-offset: 4px;
    margin-bottom: 14px;
  }
  .services-list { font-size: 17px; font-weight: 500; letter-spacing: 0.4px; }

  /* Wordmark */
  .wordmark {
    display: flex; align-items: center; gap: 14px;
    font-weight: 600; text-transform: uppercase; line-height: 1.1;
  }
  .wordmark__square { width: 22px; height: 22px; background: currentColor; flex: none; }
  .wordmark__name { font-size: 30px; letter-spacing: 3px; text-align: left; }
  .wordmark__name small { display: block; font-size: 30px; letter-spacing: 3px; }

  /* Front of card */
  .card--front {
    background: linear-gradient(180deg, var(--paper) 0%, #f6f6f6 60%, var(--paper-shade) 100%);
    color: var(--ink);
  }
  .card--front .wordmark {
    position: absolute; top: 58px; left: 50%; transform: translateX(-50%);
    color: var(--brand-navy);
  }
  .card--front .wordmark__name, .card--front .wordmark__name small { font-size: 26px; }
  .identity {
    position: absolute; left: 190px; top: 212px; width: 200px; text-align: left;
  }
  .identity__name { color: var(--brand-blue-deep); font-size: 19px; font-weight: 600; margin-bottom: 4px; }
  .identity__role { font-size: 14.5px; line-height: 1.35; color: var(--ink-soft); }
  .divider {
    position: absolute; left: 398px; top: 196px; width: 2px; height: 96px;
    background: linear-gradient(180deg, transparent, var(--brand-blue-deep), transparent);
  }
  .contacts { position: absolute; left: 422px; top: 200px; list-style: none; }
  .contacts li {
    display: flex; align-items: center; gap: 12px;
    font-size: 15px; color: var(--ink); margin-bottom: 9px;
  }
  .contacts svg { width: 16px; height: 16px; fill: var(--brand-blue-deep); flex: none; }
  .rule-upper {
    position: absolute; left: 422px; right: 0; top: 306px; height: 1.5px; background: var(--rule);
  }
  .company {
    position: absolute; left: 0; right: 0; top: 334px;
    display: flex; align-items: center; gap: 16px;
  }
  .company__line { flex: 1; height: 1.5px; background: var(--rule); }
  .company__text { text-align: center; }
  .company__name { color: var(--brand-blue-deep); font-size: 17px; font-weight: 600; }
  .company__address { font-size: 16px; color: var(--ink); margin-top: 2px; }
</style>
</head>
<body>
<main class="sheet">
  <section class="card card--back" aria-label="Verso de la carte">
    <div class="wordmark">
      <span class="wordmark__square"></span>
      <span class="wordmark__name">Claireval<small>Conseil et Comptes</small></span>
    </div>
    <p class="services-title">OUR SERVICES ARE</p>
    <p class="services-list">ACCOUNTING, TAX, AUDIT AND FINANCIAL MANAGEMENT</p>
  </section>

  <section class="card card--front" aria-label="Recto de la carte">
    <div class="wordmark">
      <span class="wordmark__square"></span>
      <span class="wordmark__name">Claireval<small>Conseil et Comptes</small></span>
    </div>

    <div class="identity">
      <p class="identity__name">Tomas Varenholt</p>
      <p class="identity__role">Directeur et Fondateur<br>Expert-comptable diplômé</p>
    </div>
    <div class="divider"></div>

    <ul class="contacts">
      <li>
        <svg viewBox="0 0 16 16" aria-hidden="true"><path d="M1 5c0-2 3-3 7-3s7 1 7 3v1h-4V5H5v1H1zM3 7h10l2 6H1z"/></svg>
        022 418 57 34
      </li>
      <li>
        <svg viewBox="0 0 16 16" aria-hidden="true"><path d="M1 3h14v10H1zM2 4l6 5 6-5v-.2H2z" fill-rule="evenodd"/></svg>
        tv@clairevalconseil.ch
      </li>
      <li>
        <svg viewBox="0 0 16 16" aria-hidden="true"><circle cx="8" cy="8" r="7"/><path d="M1 8h14M8 1c3 3 3 11 0 14M8 1c-3 3-3 11 0 14" stroke="#fff" stroke-width="1" fill="none"/></svg>
        www.clairevalconseil.ch
      </li>
    </ul>
    <div class="rule-upper"></div>

    <div class="company">
      <span class="company__line"></span>
      <div class="company__text">
        <p class="company__name">Brightwell Advisory and Ledger SA</p>
        <p class="company__address">Rue des Vergières 27, 1201 Genève</p>
      </div>
      <span class="company__line"></span>
    </div>
  </section>
</main>
</body>
</html>
```